Web Design Project for a Software & Consulting Company

We have just completed a recent ArtHerdly project for a new logo (see attached).
As the next stage of our rebranding we now require a website re-design to complement the new logo.
Our current site, http://www.corvinsoft.example was built in-house and does not come across as professional as we would like. We supply software and associated services to some of the world’s largest oil companies and we need our site to reflect that level of client.
We will also be posting another design project for brochures, PowerPoint slides and other materials very soon.
We would like designs for…
Home page
Product page
• TZQ
• BLV
• PNJ
Services
News page
About Us page
Contact Us page
Page for mobile devices that gives basic company and product information
Currently the site is small but we intend to increase content to include white papers etc. this should be taken into account when designing the navigation therefore we would prefer navigation through styled text links rather than images.
Colour schemes should broadly be taken from our new logo, where the dark blue and dark green from the left and right sides of the logo are the main colours, but other, brighter accent colours can be used to highlight sections or content.
Dark Blue = C:88, M:55, Y:44, K:28
Dark Green = C:87, M:53, Y:50, K:50
NB: Don’t use the logo on our current site, make sure you use the one attached.
We would prefer the final file format to be a layered PSD.
The site should be clean and professional and communicate the following...
• That we have a great depth and breadth of knowledge about our customers’ business, enabling us to deliver the best systems and solutions.
• That we are a leading provider of cost estimation and control solutions to the oil and gas industry.
• The benefits of our software and consulting services.
• Show that we deliver outstanding customer service and value with a very high level of professionalism
• The site should have no Flash and be able to self-adjust to fit any screen size.
Things to avoid …
• Obvious and clichéd oil industry imagery, no oil rigs
• Cartoon style graphics
Our Background
We are an integrated software and consulting organization specialising in the drilling side of the oil and gas industry. Simply put our software helps companies better understand, predict and communicate the cost of drilling wells.
We have 3 software products and a consulting offering consisting of…
• TZQ - Probabilistic time and cost software
• BLV – Cost tracking and reporting software
• PNJ – (currently known as DrillSavant) – Lessons learned software
• Consulting services
Our systems are in use in over 30 countries with a broad range of clients including: GN, Marovel, Dunt, Koruna, VELO Sirkami, FALUMI and Quintex.
Our current site can be found at www.corvinsoft.example
Our main competitors are
• http://www.drovanic.example/
• http://www.sumbrask.example/
• http://www.kve.example/services/software-solutions/p1-
Our depth of drilling knowledge, quality of software and collaboration with clients differentiate us form the competition.
We strive for very high levels of customer service.
We look forward to receiving your designs!
Updates
Thanks to all the designers who have submitted a design, we appreciate the effort.
We will do our best to give individual feedback on each design but given that many are quite similar we thought we would give some general feedback first.
Nearly all the designs submitted so far have been slight variations on…
-
Top Menu
-
Scrolling Photo Banner
-
4 Columns
-
Body
-
Deep Footer
These designs are well executed but they are basically the same layout as our existing site and while there is nothing inherently wrong with this layout we would like to see some designs that are a bit more innovative and different. We don’t really want just a polished version of our current site.
Thanks again,
CVS
Thanks to everyone who has submitted a design, the response has been great.
We are close to making a decision so if you are intending to submit a design please do it soon, the deadline is only a few days away.
Thanks again.
CVS
Target Market(s)
Mid to high level executives
Industry/Entity Type
Oil And Gas
Look and feel

```html
<!DOCTYPE html>
<html lang="en">
<head>
<meta charset="utf-8">
<title>Corvinsoft Technologies – Home</title>
<link rel="stylesheet" href="https://fonts.googleapis.com/css2?family=Ubuntu:wght@400;500;700&family=Ubuntu+Condensed&family=Play&family=Arimo:wght@400&display=swap">
<style>
  :root {
    --teal-dark: #123f48;
    --teal-nav: #15434c;
    --teal-line: #2a5a63;
    --green-brand: #1f5a2c;
    --ink: #1a1a1a;
    --body-text: #3a3a3a;
    --grey-sub: #6d6d6d;
    --band-text: #d6e4e6;
    --white: #ffffff;
    --cell-line: #e8e8e8;
    --button: #333333;
  }
  * { box-sizing: border-box; margin: 0; padding: 0; }
  html, body { width: 1150px; height: 1200px; overflow: hidden; background: var(--white); }
  body { position: relative; font-family: "Arimo", Arial, sans-serif; color: var(--body-text); }

  /* Header */
  .brand { position: absolute; left: 142px; top: 34px; display: flex; align-items: center; gap: 12px; }
  .brand-mark { width: 56px; height: 56px; border-radius: 50%; background: var(--teal-nav); }
  .brand-name { font-family: "Ubuntu", sans-serif; font-weight: 500; color: var(--teal-nav); line-height: 1; }
  .brand-name .word { display: block; font-size: 21px; letter-spacing: -.3px; }
  .brand-name .tag { display: block; font-size: 10px; letter-spacing: 2.6px; margin-top: 4px; }

  .main-nav a { position: absolute; top: 67px; height: 30px; line-height: 30px; font-family: "Ubuntu Condensed", "Arial Narrow", sans-serif; font-size: 14.5px; color: var(--ink); text-decoration: none; white-space: nowrap; }
  .main-nav a.is-active { background: var(--teal-nav); color: var(--white); border-radius: 3px; width: 61px; text-align: center; }
  .n-home { left: 585px; } .n-about { left: 677px; } .n-news { left: 777px; } .n-solutions { left: 854px; } .n-contact { left: 958px; }

  /* Hero */
  .hero { position: absolute; left: 115px; top: 146px; width: 931px; height: 306px;
    background: linear-gradient(90deg, #f2f2f2 0%, #e9eaea 35%, #b9b4ae 55%, #6f645a 72%, #2a2a2c 100%);
    border: 1px solid #dcdcdc; }
  .hero-title { position: absolute; left: 30px; top: 94px; font-family: "Play", sans-serif; font-size: 30px; line-height: 34px; color: var(--ink); font-weight: 400; }

  /* Feature band */
  .features { position: absolute; left: 115px; top: 452px; width: 931px; height: 113px; background: var(--teal-dark); display: flex; }
  .feature { position: relative; height: 100%; border-right: 1px solid var(--teal-line); padding-top: 14px; }
  .feature:last-child { border-right: none; }
  .feature svg { position: absolute; left: 12px; top: 15px; }
  .feature h3 { font-family: "Ubuntu", sans-serif; font-weight: 400; font-size: 14.5px; color: var(--white); margin-left: 50px; white-space: nowrap; }
  .feature p { font-family: "Ubuntu", sans-serif; font-size: 11.5px; line-height: 13px; color: var(--band-text); margin: 6px 10px 0 50px; }
  .feature a { position: absolute; left: 50px; bottom: 12px; font-family: "Ubuntu", sans-serif; font-size: 11.5px; color: var(--band-text); }
  .f1 { width: 220px; } .f2 { width: 239px; } .f3 { width: 233px; } .f4 { width: 239px; }

  /* Welcome */
  .welcome { position: absolute; left: 130px; top: 590px; width: 590px; }
  .welcome h1 { font-family: "Ubuntu", sans-serif; font-weight: 400; font-size: 24px; line-height: 30px; color: var(--ink); }
  .welcome h1 span { color: var(--green-brand); }
  .welcome p { width: 582px; font-size: 11.5px; line-height: 19.1px; margin: 0 0 19px 2px; color: var(--body-text); letter-spacing: .1px; }
  .welcome .lead { margin-top: 23px; }
  .btn-more { position: absolute; left: 2px; top: 248px; width: 95px; height: 33px; background: var(--button); color: var(--white); font-family: "Ubuntu", sans-serif; font-style: italic; font-size: 12.5px; display: flex; align-items: center; justify-content: center; border-radius: 2px; text-decoration: none; }

  /* Clients */
  .clients { position: absolute; left: 750px; top: 588px; width: 295px; text-align: center; }
  .clients h2 { font-family: "Ubuntu", sans-serif; font-weight: 700; font-size: 29px; line-height: 34px; color: var(--ink); letter-spacing: -.8px; }
  .clients .sub { font-family: "Ubuntu Condensed", "Arial Narrow", sans-serif; font-size: 15px; color: var(--grey-sub); margin-top: 0; white-space: nowrap; }
  .client-grid { display: grid; grid-template-columns: repeat(3, 1fr); grid-template-rows: 64px 76px 74px; margin-top: 12px; }
  .client-grid div { display: flex; align-items: center; justify-content: center; border-right: 1px solid var(--cell-line); border-bottom: 1px solid var(--cell-line); font-family: "Ubuntu", sans-serif; font-weight: 500; font-size: 15px; color: #2f4f55; }
  .client-grid div:nth-child(3n) { border-right: none; }
  .client-grid div:nth-child(n+7) { border-bottom: none; }

  /* Footer */
  .site-footer { position: absolute; left: 115px; top: 916px; width: 931px; height: 284px; background: var(--teal-dark); color: var(--white); }
  .col-title { font-family: "Ubuntu Condensed", "Arial Narrow", sans-serif; font-weight: 400; font-size: 15px; padding-bottom: 5px; border-bottom: 2px solid var(--teal-line); white-space: nowrap; }
  .office { position: absolute; top: 22px; font-family: "Ubuntu", sans-serif; }
  .office .col-title { width: 142px; }
  .office p { font-size: 11.5px; line-height: 16.5px; margin-top: 6px; color: #eef4f5; white-space: nowrap; }
  .o-eu { left: 29px; } .o-na { left: 224px; }
  .partner { position: absolute; left: 439px; top: 20px; width: 218px; }
  .partner-badge { width: 180px; height: 48px; margin: 14px 0 0 3px; border-radius: 4px; background: #2a5860; }
  .footer-rule { position: absolute; left: 26px; top: 141px; width: 645px; border-top: 2px solid var(--teal-line); }
  .footer-note { position: absolute; left: 26px; top: 157px; width: 640px; font-size: 11.5px; line-height: 14.3px; color: #eef4f5; letter-spacing: -.15px; }

  .contact-form { position: absolute; left: 706px; top: 16px; width: 200px; }
  .contact-form h4 { font-family: "Ubuntu", sans-serif; font-weight: 400; font-size: 19px; padding-bottom: 6px; background: linear-gradient(90deg, #2c8aa0, rgba(44,138,160,0)) bottom/100% 1px no-repeat; }
  .field { display: block; width: 199px; height: 26px; margin-top: 8px; background: var(--white); border: 1px solid #c9c9c9; border-radius: 2px; font-family: "Ubuntu", sans-serif; font-size: 12px; color: #333; padding: 5px 10px; }
  .contact-form .field:first-of-type { margin-top: 14px; }
  .field.message { height: 60px; position: relative; }
  .field.message svg { position: absolute; right: 4px; bottom: 4px; }
  .submit { position: absolute; right: 0; top: 183px; width: 65px; height: 24px; background: linear-gradient(#ffffff, #dedede); border: 1px solid #bbb; border-radius: 2px; font-family: "Ubuntu", sans-serif; font-size: 10.5px; color: #111; display: flex; align-items: center; justify-content: center; }

  .footer-bottom { position: absolute; left: 0; top: 241px; width: 931px; border-top: 1px solid #0e343b; padding: 13px 26px 0 26px; display: flex; justify-content: space-between; font-family: "Ubuntu", sans-serif; font-size: 11px; color: #eef4f5; }
  .footer-bottom .sep { margin: 0 9px; }
</style>
</head>
<body>

<header>
  <div class="brand">
    <span class="brand-mark"></span>
    <span class="brand-name"><span class="word">CORVINSOFT</span><span class="tag">TECHNOLOGIES</span></span>
  </div>
  <nav class="main-nav">
    <a class="n-home is-active" href="#">HOME</a>
    <a class="n-about" href="#">ABOUT US</a>
    <a class="n-news" href="#">NEWS</a>
    <a class="n-solutions" href="#">SOLUTIONS</a>
    <a class="n-contact" href="#">CONTACT US</a>
  </nav>
</header>

<section class="hero" role="img" aria-label="Photo of two smiling business professionals in dark suits against a bright office background">
  <h2 class="hero-title">Well Knowledge Lessons<br>Learned for the Oil and<br>Gas Industry!</h2>
</section>

<section class="features">
  <div class="feature f1">
    <svg width="28" height="32" viewBox="0 0 28 32" fill="none" stroke="#fff" stroke-width="2"><circle cx="14" cy="14" r="6"/><path d="M11 20v4h6v-4M12 27h4"/><path d="M14 2v3M4 6l2 2M24 6l-2 2M1 14h3M24 14h3"/></svg>
    <h3>Time &amp; Cost Estimation</h3>
    <p>TZQ delivers a standardized, systematic approach to under­standing, quantifying..</p>
    <a href="#">Read More</a>
  </div>
  <div class="feature f2">
    <svg width="26" height="30" viewBox="0 0 26 30" fill="none" stroke="#fff" stroke-width="2"><rect x="3" y="2" width="20" height="26" rx="2"/><rect x="7" y="6" width="12" height="5"/><path d="M7 15h2M12 15h2M17 15h2M7 19h2M12 19h2M17 19h2M7 23h2M12 23h2M17 23h2"/></svg>
    <h3>Materials and Cost Control</h3>
    <p>Since 1992 BLV has been helping companies optimize their materi­als ..</p>
    <a href="#">Read More</a>
  </div>
  <div class="feature f3">
    <svg width="26" height="30" viewBox="0 0 26 30" fill="none" stroke="#fff" stroke-width="2.4"><rect x="3" y="2" width="20" height="26" rx="2"/><path d="M8 9h10M8 15h10M8 21h10"/></svg>
    <h3>Lessons Learned</h3>
    <p>DrillSavant is an advanced lessons learned and knowledge management..</p>
    <a href="#">Read More</a>
  </div>
  <div class="feature f4">
    <svg width="30" height="30" viewBox="0 0 30 30" fill="none" stroke="#fff" stroke-width="2"><circle cx="15" cy="15" r="13"/><path d="M7 9c3 1 4 3 3 6s2 4 1 7M18 4c-1 3 2 4 4 4s3 3 1 5-1 5-3 6"/></svg>
    <h3>Services and Cosulting</h3>
    <p>Software solutions rely on people and processes to deliver results..</p>
    <a href="#">Read More</a>
  </div>
</section>

<section class="welcome">
  <h1>Welcome to <span>Corvinsoft Technologies</span></h1>
  <p class="lead">Corvinsoft Technologies have developed and continue to support software in over 30 countries, providing real results to hundreds of drilling operations. With decades of hands-on software and well engineering experience, we are uniquely positioned to provide the right solution to our customers.</p>
  <p>We are an integrated software and consulting organization, helping companies across the globe to better manage the Business of Drilling Wells, improving capital allocation and saving money.</p>
  <p>Our systems are in use in over 30 countries with a broad range of clients including: GN, Marovel, Halvetta, Koruna, Dunt, FALUMI and Quintex.</p>
  <a class="btn-more" href="#">Learn More..</a>
</section>

<aside class="clients">
  <h2>RECENT CLIENTS</h2>
  <p class="sub">TRUST US WITH THEIR &nbsp;CUSTOMERS</p>
  <div class="client-grid">
    <div>Koruna</div>
    <div>GN</div>
    <div>Halvetta</div>
    <div>VELO</div>
    <div>Dunt</div>
    <div>Marovel</div>
    <div>FALUMI</div>
    <div>Brenmore</div>
    <div>Tessaly</div>
  </div>
</aside>

<footer class="site-footer">
  <div class="office o-eu">
    <h4 class="col-title">EUROPE</h4>
    <p>18 Tarrow Lane<br>Kelmere, KM4 2RT<br>Phone:+44(0)1632 960481<br>Email:eu@corvinsoft.example</p>
  </div>
  <div class="office o-na">
    <h4 class="col-title">NORTH AMERICA</h4>
    <p>4100 Larkfield Pkwy, Suite 210<br>Brenton, TX 77999<br>Phone:(555) 014 2278<br>Email:us@corvinsoft.example</p>
  </div>
  <div class="partner">
    <h4 class="col-title">OUR GOLD BUSINESS PARTNER</h4>
    <div class="partner-badge" role="img" aria-label="Partner certification badge"></div>
  </div>
  <div class="footer-rule"></div>
  <p class="footer-note">Lorem ipsum dolor sit amet, consectetur adipiscing elit. Donec semper nisl eget ante vehicula at viverra est porta. Morbi eleifend, turpis eget vehicula porta, leo velit facilisis justo, quis vehicula velit erat nec est. Pellentesque habitant morbi tristique senectus et netus et malesuada fames ac turpis egestas. Pellentesque consequat est vel metus luctus com­modo. In hac habitasse platea dictumst. Suspendisse justo ipsum,</p>

  <form class="contact-form">
    <h4>Get in touch</h4>
    <div class="field">Name</div>
    <div class="field">E-mail</div>
    <div class="field message">Message
      <svg width="8" height="8" viewBox="0 0 8 8" stroke="#999"><path d="M1 7L7 1M4 7L7 4"/></svg>
    </div>
    <div class="submit">SUBMIT</div>
  </form>

  <div class="footer-bottom">
    <span>Privacy Policy<span class="sep">|</span>Terms &amp; Conditions</span>
    <span>© Copyrights 2012 Corvinsoft</span>
  </div>
</footer>

</body>
</html>
```